WEBSITE & LOGO for MEDICAL CILINC

BRAND NAME ( LUMORA) Medical clinic for intravenous (IV) vitamin hydration and wellness therapy. range of signature infusions and boosters are targeted at preventative health and wellness – essentially replenishing your body with the fluids and vitamins it needs to be in tip-top condition.

Blood testing
laboratory analysis
IV therapy
IV infusion drips
phlebotomy services
nurses for Home care services
Patient repatriation services to their countries
Hire of medical equipments including beds and wheel chairs

www.quellsa.com
www.tovexclinic.com
http://pickaflask.co.uk

All adults
18+ women and men.

No black color in the background
DNA double helix image should to be implemented in the design and logo.
the website should be easy to be used so the clients can add to the shopping cart
- select treatment or drips
- supplement
- book nurses
- book home visit
- book nurse for international home care journey

Colors
86cae7
33b8a4
e4daeb
f9d9e8
fefafc
fbd2d3
eee9f4
85acd3
0455a3

Requirements
Must have
• DNA Double helix in Java animation
injection icon for IV injection
Infusion Icon Bag for IV infusion
Analysis icon
phlebotomy services icon
Patient repatriation services icon
Hire of medical equipments icon

light background and water blue menu and buttons with highlights
Nice to have
• dynamic website where
IV injections scroll from side to side
IV infusion scroll from side to side.

```html
<!DOCTYPE html>
<html lang="en">
<head>
<meta charset="utf-8">
<title>Lumora – IV Therapy &amp; Wellness Clinic</title>
<link href="https://fonts.googleapis.com/css2?family=Jost:wght@400;500&family=Lato:wght@400;700&display=swap" rel="stylesheet">
<style>
:root{
  --navy:#0455a3;
  --deep:#0b4a9c;
  --teal:#33b8a4;
  --sky:#86cae7;
  --blush:#fdf6f8;
  --slot:#e6eef7;
  --ink:#333a44;
  --muted:#5c6470;
  --line:#e4e4ea;
  --white:#ffffff;
}
*{box-sizing:border-box;margin:0;padding:0}
html,body{width:1200px;height:4011px;overflow:hidden}
body{font-family:"Lato",sans-serif;color:var(--ink);background:var(--white);position:relative}
section,header,footer,nav{position:absolute;left:0;width:1200px}
.abs{position:absolute}
.heading{font-family:"Jost",sans-serif;font-weight:400;color:var(--navy);text-align:center}
.rule{width:56px;height:2px;background:var(--navy);margin:14px auto 0}

/* header */
.site-header{top:0;height:123px;background:var(--white)}
.brand{left:110px;top:32px;display:flex;align-items:center;gap:12px}
.brand-dot{width:40px;height:40px;border-radius:50%;background:var(--navy)}
.brand-name{font-family:"Jost",sans-serif;font-size:40px;color:var(--navy)}
.call{left:823px;top:31px;display:flex;align-items:center;gap:14px;font-family:"Jost",sans-serif;font-size:21px;color:var(--ink)}
.call-icon{width:60px;height:60px;border-radius:50%;background:var(--teal);display:flex;align-items:center;justify-content:center}

/* nav */
.main-nav{top:123px;height:62px;background:var(--deep)}
.main-nav ul{list-style:none;position:absolute;left:110px;top:0;height:62px;display:flex}
.main-nav li{height:62px;display:flex;align-items:center;font-family:"Jost",sans-serif;font-size:12px;color:var(--white);text-transform:uppercase;padding:0 31px}
.main-nav li.active{background:var(--teal);padding:0 40px}
.cart{left:985px;top:0;height:62px;display:flex;align-items:center;gap:6px;color:var(--white);font-family:"Jost",sans-serif;font-size:15px}
.cart-sep{left:964px;top:23px;width:1px;height:16px;background:rgba(255,255,255,.6)}

/* hero */
.hero{top:185px;height:688px;background:linear-gradient(135deg,#0a3f8c 0%,#0b6fc0 45%,#1aa2dc 75%,#0a4f9f 100%)}
.hero-title{top:220px;width:100%;text-align:center;font-family:"Jost",sans-serif;font-size:104px;color:var(--white);line-height:1}
.hero-sub{top:330px;width:100%;text-align:center;font-family:"Jost",sans-serif;font-size:43px;color:var(--white)}
.btn-outline{display:flex;align-items:center;justify-content:center;border:2px solid var(--white);border-radius:30px;color:var(--white);font-family:"Jost",sans-serif}
.hero .btn-outline{left:492px;top:414px;width:216px;height:56px;font-size:20px}

/* welcome */
.welcome{top:873px;height:571px;background:linear-gradient(180deg,#f6f6f8,#eeeef2)}
.welcome .heading{position:absolute;top:64px;width:100%;font-size:42px}
.welcome-text{top:160px;left:0;width:1200px;text-align:center;font-size:12.5px;line-height:31px;color:var(--ink);white-space:nowrap}
.welcome-text p+p{margin-top:31px}
.btn-solid{display:flex;align-items:center;justify-content:center;background:var(--navy);border-radius:30px;color:var(--white);font-family:"Jost",sans-serif}
.welcome .btn-solid{left:494px;top:437px;width:213px;height:58px;font-size:19px}

/* treatment */
.treatment{top:1444px;height:478px;background:var(--white)}
.treatment-photo{left:0;top:0;width:610px;height:478px;background:radial-gradient(circle at 45% 40%,#1f7fc6 0%,#0c3566 45%,#06142b 100%)}
.treatment h2{left:673px;top:52px;font-family:"Jost",sans-serif;font-weight:400;font-size:38px;color:var(--navy)}
.treatment .bar{left:673px;top:107px;width:58px;height:2px;background:var(--navy)}
.treat-list{left:673px;top:136px;list-style:none}
.treat-list li{height:41px;display:flex;align-items:center;gap:16px;font-size:13px;color:var(--ink)}
.treatment .btn-solid{left:677px;top:397px;width:160px;height:50px;font-size:18px}

/* services */
.services{top:1922px;height:801px;background:var(--blush)}
.services .heading{position:absolute;top:50px;width:100%;font-size:40px}
.card{position:absolute;width:234px;height:270px;background:var(--white);border:1px solid var(--line);box-shadow:0 1px 4px rgba(0,0,0,.06);text-align:center}
.icon-slot{display:block;width:70px;height:70px;margin:30px auto 0;border-radius:8px;background:var(--slot)}
.card h3{font-family:"Jost",sans-serif;font-weight:400;font-size:17px;color:var(--ink);margin-top:10px;line-height:21px}
.card p{font-size:11px;line-height:23px;color:var(--muted);margin:14px 18px 0}

/* booking band */
.journey{top:2723px;height:346px;background:linear-gradient(110deg,#2fae9f 0%,#1e8fa7 40%,#0d5ea6 75%,#0a4a9b 100%);text-align:center;color:var(--white);font-family:"Jost",sans-serif}
.journey h2{position:absolute;top:72px;width:100%;font-weight:400;font-size:48px}
.journey p{position:absolute;top:145px;width:100%;font-size:41px}
.journey .btn-outline{left:496px;top:227px;width:206px;height:58px;font-size:18px}

/* news */
.news{top:3069px;height:566px;background:var(--white)}
.news .heading{position:absolute;top:44px;width:100%;font-size:38px}
.post{position:absolute;top:138px;width:470px;height:361px;border:1px solid var(--line)}
.post-img{left:0;top:0;width:468px;height:220px}
.post-date{left:0;top:185px;height:35px;padding:0 26px 0 16px;background:var(--teal);color:var(--white);font-size:14px;display:flex;align-items:center;clip-path:polygon(0 0,88% 0,100% 100%,0 100%)}
.post h3{position:absolute;left:22px;top:242px;font-family:"Jost",sans-serif;font-weight:400;font-size:19px;color:var(--ink)}
.post p{position:absolute;left:22px;top:286px;width:420px;font-size:12px;line-height:25px;color:var(--ink)}
.post p b{color:var(--navy);font-weight:700}

/* footer */
.site-footer{top:3635px;height:376px;background:var(--deep);color:var(--white)}
.foot-brand{left:146px;top:80px;display:flex;align-items:center;gap:12px}
.foot-brand .brand-dot{background:var(--white)}
.foot-brand .brand-name{color:var(--white)}
.social{left:146px;top:202px;display:flex;gap:8px}
.social span{width:36px;height:36px;border:1.5px solid var(--white);border-radius:50%}
.col-title{font-family:"Jost",sans-serif;font-size:18px}
.links{list-style:none;font-size:12px}
.links li{height:26.5px;display:flex;align-items:center;gap:12px}
.contact-row{display:flex;align-items:flex-start;gap:18px;font-size:13px;line-height:22px}
.contact-ico{width:30px;height:30px;border-radius:50%;background:rgba(255,255,255,.14);display:flex;align-items:center;justify-content:center;flex:none}
.email-box{left:868px;top:167px;width:220px;height:40px;background:var(--white);color:#999;font-size:11px;padding:13px 10px}
.submit{left:868px;top:222px;width:86px;height:32px;background:var(--teal);font-size:12px;font-weight:700;display:flex;align-items:center;justify-content:center}
.copyright{top:334px;width:100%;text-align:center;font-size:13px}
</style>
</head>
<body>

<header class="site-header">
  <div class="abs brand"><span class="brand-dot"></span><span class="brand-name">Lumora</span></div>
  <div class="abs call">
    <span class="call-icon"><svg width="22" height="22" viewBox="0 0 24 24"><path fill="#fff" d="M6.6 10.8a15 15 0 0 0 6.6 6.6l2.2-2.2c.3-.3.7-.4 1-.2 1.1.4 2.3.6 3.6.6.6 0 1 .4 1 1V20c0 .6-.4 1-1 1A17 17 0 0 1 3 4c0-.6.4-1 1-1h3.5c.6 0 1 .4 1 1 0 1.3.2 2.5.6 3.6.1.3 0 .7-.2 1z"/></svg></span>
    Call Us : 000-555-0190
  </div>
</header>

<nav class="main-nav">
  <ul>
    <li class="active">Home</li><li>About Us</li><li>Services</li><li>Features</li><li>News</li><li>Testimonials</li><li>Contact Us</li>
  </ul>
  <span class="abs cart-sep"></span>
  <div class="abs cart"><svg width="16" height="14" viewBox="0 0 16 14"><path fill="#fff" d="M0 0h3l.6 2H16l-2 6H5l.5 2H14v1.5H4.3L1.9 1.5H0z"/><circle cx="6" cy="12.8" r="1.2" fill="#fff"/><circle cx="12.5" cy="12.8" r="1.2" fill="#fff"/></svg>(0) items</div>
</nav>

<section class="hero" role="img" aria-label="Glowing blue DNA double helix over a field of digital numbers">
  <div class="abs hero-title">Lumora</div>
  <div class="abs hero-sub">Sed ut perspiciatis unde omnis iste</div>
  <div class="abs btn-outline">Learn More</div>
</section>

<section class="welcome">
  <h2 class="heading">Welcome to Lumora<div class="rule"></div></h2>
  <div class="abs welcome-text">
    <p>Sed ut perspiciatis unde omnis iste natus error sit voluptatem accusantium doloremque laudantium, totam<br>rem aperiam, eaque ipsa quae ab illo inventore veritatis et quasi architecto beatae vitae dicta sunt explicabo.<br>Nemo enim ipsam voluptatem quia voluptas sit aspernatur aut odit aut fugit, sed quia consequuntur magni<br>dolores eos qui ratione voluptatem sequi nesciunt.</p>
    <p>Neque porro quisquam est, qui dolorem ipsum quia dolor sit amet, consectetur, adipisci velit, sed quia non<br>numquam eius modi tempora incidunt ut labore et dolore magnam aliquam quaerat voluptatem.Ut enim ad<br>veniam, quis nostrum exercitationem ullam corporis suscipit laboriosam</p>
  </div>
  <div class="abs btn-solid">Book Home Visit</div>
</section>

<section class="treatment">
  <div class="abs treatment-photo" role="img" aria-label="Glowing DNA helix floating above an open hand on a dark blue background"></div>
  <h2 class="abs">Select Treatment</h2>
  <span class="abs bar"></span>
  <ul class="abs treat-list">
    <li><svg width="13" height="13" viewBox="0 0 13 13"><circle cx="6.5" cy="6.5" r="5.5" fill="none" stroke="#0455a3" stroke-width="1.5"/><path d="M4 6.5h5M6.8 4.5l2 2-2 2" fill="none" stroke="#0455a3" stroke-width="1.3"/></svg>Sed ut perspiciatis unde omnis iste natus error sit</li>
    <li><svg width="13" height="13" viewBox="0 0 13 13"><circle cx="6.5" cy="6.5" r="5.5" fill="none" stroke="#0455a3" stroke-width="1.5"/><path d="M4 6.5h5M6.8 4.5l2 2-2 2" fill="none" stroke="#0455a3" stroke-width="1.3"/></svg>Voluptatem accusa ntium doloremque</li>
    <li><svg width="13" height="13" viewBox="0 0 13 13"><circle cx="6.5" cy="6.5" r="5.5" fill="none" stroke="#0455a3" stroke-width="1.5"/><path d="M4 6.5h5M6.8 4.5l2 2-2 2" fill="none" stroke="#0455a3" stroke-width="1.3"/></svg>Laudantium, totam rem aperiam, eaque</li>
    <li><svg width="13" height="13" viewBox="0 0 13 13"><circle cx="6.5" cy="6.5" r="5.5" fill="none" stroke="#0455a3" stroke-width="1.5"/><path d="M4 6.5h5M6.8 4.5l2 2-2 2" fill="none" stroke="#0455a3" stroke-width="1.3"/></svg>Ipsa quae ab &nbsp;inventore veritatis et quasi</li>
    <li><svg width="13" height="13" viewBox="0 0 13 13"><circle cx="6.5" cy="6.5" r="5.5" fill="none" stroke="#0455a3" stroke-width="1.5"/><path d="M4 6.5h5M6.8 4.5l2 2-2 2" fill="none" stroke="#0455a3" stroke-width="1.3"/></svg>Architecto beatae vitae dicta sunt explicabo.</li>
    <li><svg width="13" height="13" viewBox="0 0 13 13"><circle cx="6.5" cy="6.5" r="5.5" fill="none" stroke="#0455a3" stroke-width="1.5"/><path d="M4 6.5h5M6.8 4.5l2 2-2 2" fill="none" stroke="#0455a3" stroke-width="1.3"/></svg>Nemo enim ipsam voluptatem quia voluptas</li>
  </ul>
  <div class="abs btn-solid">Supplement</div>
</section>

<section class="services">
  <h2 class="heading">Our Services<div class="rule"></div></h2>

  <div class="card" style="left:110px;top:151px">
    <span class="icon-slot" role="img" aria-label="Blood testing icon"></span>
    <h3>Blood Testing</h3>
    <p>Sed ut perspiciatis unde omnis iste natus error sit voluptatem accu doloremque laudantium</p>
  </div>
  <div class="card" style="left:358px;top:151px">
    <span class="icon-slot" role="img" aria-label="Laboratory analysis icon"></span>
    <h3>Laboratory Analysis</h3>
    <p>Sed ut perspiciatis unde omnis iste natus error sit voluptatem accu doloremque laudantium</p>
  </div>
  <div class="card" style="left:606px;top:151px">
    <span class="icon-slot" role="img" aria-label="IV therapy injection icon"></span>
    <h3>IV therapy</h3>
    <p>Sed ut perspiciatis unde omnis iste natus error sit voluptatem accu doloremque laudantium</p>
  </div>
  <div class="card" style="left:854px;top:151px">
    <span class="icon-slot" role="img" aria-label="IV infusion bag icon"></span>
    <h3>IV infusion drips</h3>
    <p>Sed ut perspiciatis unde omnis iste natus error sit voluptatem accu doloremque laudantium</p>
  </div>

  <div class="card" style="left:110px;top:453px">
    <span class="icon-slot" role="img" aria-label="Phlebotomy services icon"></span>
    <h3>Phlebotomy Services</h3>
    <p>Sed ut perspiciatis unde omnis iste natus error sit voluptatem accu doloremque laudantium</p>
  </div>
  <div class="card" style="left:358px;top:453px">
    <span class="icon-slot" role="img" aria-label="Home care nurses icon"></span>
    <h3>Nurses for<br>Home care services</h3>
    <p>iste natus error sit voluptatem accu doloremque laudantium</p>
  </div>
  <div class="card" style="left:606px;top:453px">
    <span class="icon-slot" role="img" aria-label="Patient repatriation icon"></span>
    <h3>Patient repatriation<br>services to their countries</h3>
    <p>iste natus error sit voluptatem accu doloremque laudantium</p>
  </div>
  <div class="card" style="left:854px;top:453px">
    <span class="icon-slot" role="img" aria-label="Medical equipment hire icon"></span>
    <h3>Hire of medical<br>equipments including beds<br>&amp; wheelchairs</h3>
    <p>iste natus error sit voluptatem accu doloremque laudantium</p>
  </div>
</section>

<section class="journey">
  <h2>Book Nurse for International</h2>
  <p>Home Care Journey</p>
  <div class="abs btn-outline">LEARN MORE</div>
</section>

<section class="news">
  <h2 class="heading">Latest News<div class="rule"></div></h2>
  <article class="post" style="left:110px">
    <div class="abs post-img" role="img" aria-label="Blue glass test tube containing a DNA strand" style="background:linear-gradient(135deg,#7fc4f2,#1869c9 50%,#0a3e8e)"></div>
    <div class="abs post-date">02 MARCH 2020</div>
    <h3>Sed ut perspiciatis unde omnis</h3>
    <p>Nemo enim ipsam voluptatem quia voluptas sit aspernatur aut odit aut ratione voluptatem sequi nesciunt. <b>READ MORE</b></p>
  </article>
  <article class="post" style="left:618px">
    <div class="abs post-img" role="img" aria-label="Glowing DNA helix and molecule structures on a dark blue background" style="background:linear-gradient(135deg,#0a1f4a,#14509a 55%,#0b2a5e)"></div>
    <div class="abs post-date">02 MARCH 2020</div>
    <h3>Sed ut perspiciatis unde omnis</h3>
    <p>Nemo enim ipsam voluptatem quia voluptas sit aspernatur aut odit aut ratione voluptatem sequi nesciunt. <b>READ MORE</b></p>
  </article>
</section>

<footer class="site-footer">
  <div class="abs foot-brand"><span class="brand-dot"></span><span class="brand-name">Lumora</span></div>
  <div class="abs social"><span></span><span></span><span></span><span></span><span></span></div>

  <div class="abs col-title" style="left:440px;top:62px">Quick Links</div>
  <ul class="abs links" style="left:440px;top:101px">
    <li>&#8594; HOME</li><li>&#8594; ABOUT US</li><li>&#8594; SERVICES</li><li>&#8594; FEATURES</li><li>&#8594; NEWS</li><li>&#8594; TESTIMONIALS</li><li>&#8594; CONTACT US</li>
  </ul>

  <div class="abs col-title" style="left:620px;top:62px">Contact Us</div>
  <div class="abs contact-row" style="left:620px;top:105px"><span class="contact-ico"><svg width="12" height="12" viewBox="0 0 24 24"><path fill="#fff" d="M6.6 10.8a15 15 0 0 0 6.6 6.6l2.2-2.2c.3-.3.7-.4 1-.2 1.1.4 2.3.6 3.6.6.6 0 1 .4 1 1V20c0 .6-.4 1-1 1A17 17 0 0 1 3 4c0-.6.4-1 1-1h3.5c.6 0 1 .4 1 1 0 1.3.2 2.5.6 3.6.1.3 0 .7-.2 1z"/></svg></span><span style="padding-top:4px">(312) 555-0148</span></div>
  <div class="abs contact-row" style="left:620px;top:152px"><span class="contact-ico"><svg width="13" height="10" viewBox="0 0 13 10" fill="none" stroke="#fff" stroke-width="1.2"><rect x=".6" y=".6" width="11.8" height="8.8"/><path d="M.6.6l5.9 5 5.9-5"/></svg></span><span style="padding-top:4px">info@lumora-clinic.com</span></div>
  <div class="abs contact-row" style="left:620px;top:197px"><span class="contact-ico"><svg width="10" height="13" viewBox="0 0 10 13"><path fill="#fff" d="M5 0a5 5 0 0 1 5 5c0 3.5-5 8-5 8S0 8.5 0 5a5 5 0 0 1 5-5z"/><circle cx="5" cy="5" r="1.8" fill="#0b4a9c"/></svg></span><span>2172 Lorem Ipsum<br>dummy text 32308</span></div>

  <div class="abs col-title" style="left:868px;top:62px">Newsletter</div>
  <div class="abs" style="left:868px;top:108px;width:224px;font-size:11px;line-height:23px">Sed ut perspiciatis unde omnis us error sit voluptatem</div>
  <div class="abs email-box">Email :</div>
  <div class="abs submit">SUBMIT</div>

  <div class="abs copyright">© Copyrights 2020 - Lumora.All Rights Reserved.</div>
</footer>

</body>
</html>
```